Brivane Management

We need a web design for a new consulting company, with clients all over the world. The company provides management consulting to the travel industry.

Logo files are attached.

Website must look very corporate and be responsive in design.

Management Consulting

```html
<!DOCTYPE html>
<html lang="en">
<head>
<meta charset="utf-8">
<title>Brivane Management</title>
<link rel="stylesheet" href="https://fonts.googleapis.com/css2?family=Lato:wght@400;700&family=Oswald:wght@400&display=swap">
<style>
:root{
  --navy:#15164a;
  --navy-mid:#1e2468;
  --blue:#1a73c2;
  --blue-bright:#1e8ad6;
  --green:#5fb52a;
  --ink:#1d1d1d;
  --text:#333;
  --muted:#555;
  --line:#dcdcdc;
  --white:#fff;
}
*{box-sizing:border-box;margin:0;padding:0}
html,body{width:1200px;height:1002px;overflow:hidden;background:var(--white);font-family:"Lato",sans-serif;color:var(--text)}
.page{position:relative;width:1200px;height:1002px}

/* hero */
.hero{position:absolute;left:0;top:0;width:1200px;height:492px;overflow:hidden}
.hero-photo{position:absolute;inset:0;background:linear-gradient(100deg,#8e9aa8 0%,#b7c2cc 22%,#5d6a7c 40%,#2c3548 55%,#5c6a80 100%)}
.hero-shape{position:absolute;inset:0}
.topbar{position:absolute;right:0;top:0;height:54px;width:600px;display:flex;align-items:center;padding-left:154px;color:var(--white);font-size:21px}
.topbar svg{margin-right:8px}
.navbar{position:absolute;left:145px;top:54px;width:1055px;height:68px;background:var(--white);display:flex;align-items:center}
.brand{display:flex;align-items:center;gap:10px;width:399px;padding-left:30px}
.brand-dot{width:44px;height:44px;border-radius:50%;background:var(--green);flex:0 0 44px}
.brand-name{font-family:"Lato",sans-serif;font-weight:700;font-size:24px;color:var(--navy);letter-spacing:.3px;white-space:nowrap}
.nav{display:flex;height:68px;list-style:none}
.nav li{display:flex;align-items:center;font-size:19px;color:var(--ink);padding:0 20px 0 22px}
.nav li.active{background:var(--green);color:var(--white);padding:0 6px}
.hero-copy{position:absolute;left:698px;top:168px;font-family:"Oswald",sans-serif;font-weight:400;font-size:38px;line-height:42px;color:var(--white)}
.cta{position:absolute;left:700px;top:318px;height:35px;width:208px;background:var(--white);display:flex;align-items:center;font-size:17px;font-weight:700;font-style:italic;color:var(--ink)}
.cta-arrow{width:32px;height:35px;background:var(--green);display:flex;align-items:center;justify-content:center;margin-right:10px}
.slide-btn{position:absolute;top:262px;width:38px;height:38px;border-radius:50%;background:var(--white);display:flex;align-items:center;justify-content:center;box-shadow:0 1px 3px rgba(0,0,0,.4)}
.slide-btn.prev{left:120px}
.slide-btn.next{left:1039px}

/* cards */
.card{position:absolute;top:533px;height:298px;border:1px solid var(--line);background:var(--white);padding:0 14px}
.card-about{left:140px;width:289px}
.card-do{left:462px;width:289px}
.card-new{left:785px;width:288px}
.card h2{font-size:20px;font-weight:400;color:var(--ink);padding:10px 3px 7px;border-bottom:2px solid var(--navy);width:244px;white-space:nowrap}
.card-about h2{width:250px}
.card h2 span{color:var(--blue)}
.about-photo{margin-top:12px;width:260px;height:131px;background:linear-gradient(90deg,#9fb2c4,#d6dee6 55%,#7d8fa3)}
.about-text{font-size:14px;line-height:20px;margin-top:9px;color:var(--text)}
.more{position:absolute;left:14px;bottom:14px;display:flex;height:19px;font-size:12px}
.more i{width:19px;background:#3a3a3a;display:flex;align-items:center;justify-content:center}
.more b{font-weight:400;background:var(--green);color:var(--white);padding:2px 10px 0 8px}
.do-item{display:flex;gap:10px;padding:9px 0 7px 4px;border-bottom:1px solid #e6e6e6}
.do-item:last-of-type{border-bottom:0}
.do-item svg{flex:0 0 34px}
.do-item h3{font-size:16px;font-weight:400;color:var(--blue);margin-bottom:3px}
.do-item p{font-size:12px;line-height:16px;color:var(--text)}
.news{display:flex;gap:12px;padding:14px 0 10px;border-bottom:1px dashed #bbb}
.date{width:34px;flex:0 0 34px;text-align:center;color:var(--white)}
.date .d{background:var(--blue);font-size:18px;font-weight:700;height:25px;line-height:25px}
.date .m{background:#222;font-size:10px;height:18px;line-height:18px}
.news h3{font-size:14px;font-weight:400;color:var(--ink)}
.news p{font-size:13px;color:var(--text)}
.news a{font-size:11px;font-weight:700;color:var(--blue);text-decoration:none}
.pager{position:absolute;left:18px;bottom:8px;display:flex;gap:2px}
.pager span{width:18px;height:18px;display:flex;align-items:center;justify-content:center}

/* footer */
.footer-band{position:absolute;left:0;top:862px;width:1200px;height:140px}
.footer{position:absolute;left:0;top:902px;width:1200px;height:100px;color:var(--white)}
.foot-nav{position:absolute;left:140px;top:14px;font-size:12px;font-weight:700;display:flex;gap:12px}
.foot-nav span.sep{font-weight:400}
.foot-addr{position:absolute;left:437px;top:12px;font-size:12px;line-height:18px;display:flex;gap:8px}
.foot-contact{position:absolute;left:612px;top:10px;font-size:12px;line-height:22px;white-space:nowrap}
.foot-contact div{display:flex;align-items:center;gap:7px}
.subscribe{position:absolute;left:802px;top:17px;display:flex;height:32px}
.subscribe .field{width:170px;background:var(--white);color:#999;font-size:12px;font-style:italic;display:flex;align-items:center;padding-left:32px}
.subscribe .btn{width:91px;background:var(--blue);font-size:13px;font-weight:700;display:flex;align-items:center;justify-content:center}
.copy{position:absolute;left:140px;top:76px;font-size:12px}
.social{position:absolute;left:957px;top:66px;display:flex;gap:7px}
.social span{width:21px;height:21px;border:1.5px solid var(--white);border-radius:50%}
</style>
</head>
<body>
<div class="page">

  <section class="hero">
    <div class="hero-photo" role="img" aria-label="Business person in a suit touching a screen with service words"></div>
    <svg class="hero-shape" width="1200" height="492" viewBox="0 0 1200 492">
      <path d="M640 0 H1200 V492 H1040 C780 470 560 380 505 240 C470 150 540 40 640 0Z" fill="#15164a" opacity=".9"/>
      <path d="M505 240 C560 380 780 470 1040 492" fill="none" stroke="#1a73c2" stroke-width="12"/>
    </svg>
    <div class="topbar">
      <svg width="32" height="32" viewBox="0 0 32 32"><circle cx="16" cy="16" r="15" fill="#5fb52a" stroke="#fff" stroke-width="2"/><path d="M11 9l3 0 1 4-2 1c1 2 3 4 5 5l1-2 4 1v3c-7 1-13-5-12-12z" fill="#fff"/></svg>
      123-555-0148
    </div>
    <nav class="navbar">
      <div class="brand"><span class="brand-dot"></span><span class="brand-name">BRIVANE MANAGEMENT</span></div>
      <ul class="nav">
        <li class="active">Home</li>
        <li>About Us</li>
        <li>Our Services</li>
        <li>Contact Us</li>
      </ul>
    </nav>
    <h1 class="hero-copy">We create active<br>relationships with<br>Our Clients...!</h1>
    <div class="cta"><span class="cta-arrow"><svg width="12" height="16" viewBox="0 0 12 16"><path d="M2 1l8 7-8 7" fill="none" stroke="#fff" stroke-width="3"/></svg></span>Get Started With Us !</div>
    <span class="slide-btn prev"><svg width="12" height="14" viewBox="0 0 12 14"><path d="M9 1L3 7l6 6" fill="none" stroke="#333" stroke-width="2.5"/></svg></span>
    <span class="slide-btn next"><svg width="12" height="14" viewBox="0 0 12 14"><path d="M3 1l6 6-6 6" fill="none" stroke="#333" stroke-width="2.5"/></svg></span>
  </section>

  <article class="card card-about">
    <h2>About <span>Brivane Management</span></h2>
    <div class="about-photo" role="img" aria-label="Smiling consultant with colleagues in an office"></div>
    <p class="about-text">Lorem ipsum dolor sit amet, consectetuer adipiscing elit, sed diam nonummy nibh euismod magna aliquam erat volutpat.</p>
    <div class="more"><i><svg width="10" height="8" viewBox="0 0 10 8"><path d="M0 4h8M5 1l3 3-3 3" fill="none" stroke="#fff" stroke-width="1.3"/></svg></i><b>Read More</b></div>
  </article>

  <article class="card card-do">
    <h2>What <span>We Do</span></h2>
    <div class="do-item">
      <svg width="34" height="34" viewBox="0 0 34 34"><circle cx="17" cy="10" r="5" fill="#666"/><path d="M9 24c0-6 16-6 16 0z" fill="#666"/><circle cx="6" cy="20" r="3" fill="#888"/><circle cx="28" cy="20" r="3" fill="#888"/><circle cx="17" cy="30" r="3" fill="#888"/></svg>
      <div><h3>Our Experties</h3><p>Ut wisi enim ad minim venia m, quisip<br>nostrud exerci tation ullamcor.</p></div>
    </div>
    <div class="do-item">
      <svg width="34" height="34" viewBox="0 0 34 34"><circle cx="17" cy="17" r="5" fill="#666"/><g stroke="#777" stroke-width="2"><path d="M17 3v7M17 24v7M3 17h7M24 17h7M7 7l5 5M22 22l5 5M27 7l-5 5M12 22l-5 5"/></g></svg>
      <div><h3>Our Services</h3><p>Ut wisi enim ad minim venia m, quisip<br>nostrud exerci tation ullamcor.</p></div>
    </div>
    <div class="do-item">
      <svg width="34" height="34" viewBox="0 0 34 34"><circle cx="16" cy="18" r="12" fill="none" stroke="#666" stroke-width="3"/><circle cx="16" cy="18" r="6" fill="none" stroke="#666" stroke-width="3"/><path d="M16 18L30 5" stroke="#666" stroke-width="2.5"/></svg>
      <div><h3>Our Management</h3><p>Ut wisi enim ad minim venia m, quisip<br>nostrud exerci tation ullamcor.</p></div>
    </div>
    <div class="more"><i><svg width="10" height="8" viewBox="0 0 10 8"><path d="M0 4h8M5 1l3 3-3 3" fill="none" stroke="#fff" stroke-width="1.3"/></svg></i><b>Read More</b></div>
  </article>

  <article class="card card-new">
    <h2>What's <span>New</span></h2>
    <div class="news"><div class="date"><div class="d">25</div><div class="m">OCT</div></div><div><h3>Start Orvalo Website</h3><p>Lorem ipsum dolor sit amet ellit.</p><a>Read More...</a></div></div>
    <div class="news"><div class="date"><div class="d">25</div><div class="m">OCT</div></div><div><h3>Start Orvalo Website</h3><p>Lorem ipsum dolor sit amet ellit.</p><a>Read More...</a></div></div>
    <div class="news" style="border-bottom:0"><div class="date"><div class="d">25</div><div class="m">OCT</div></div><div><h3>Start Orvalo Website</h3><p>Lorem ipsum dolor sit amet ellit.</p><a>Read More...</a></div></div>
    <div class="pager">
      <span style="background:#3a3a3a"><svg width="8" height="10" viewBox="0 0 8 10"><path d="M6 0L1 5l5 5z" fill="#fff"/></svg></span>
      <span style="background:var(--green)"><svg width="8" height="10" viewBox="0 0 8 10"><path d="M2 0l5 5-5 5z" fill="#fff"/></svg></span>
    </div>
  </article>

  <svg class="footer-band" width="1200" height="140" viewBox="0 0 1200 140">
    <path d="M0 4 L600 18 L1200 0 V140 H0Z" fill="#5fb52a"/>
    <path d="M0 40 H1200 V140 H0Z" fill="#15164a"/>
  </svg>
  <footer class="footer">
    <div class="foot-nav"><span>Home</span><span class="sep">|</span><span>About Us</span><span class="sep">|</span><span>Services</span><span class="sep">|</span><span>Contact Us</span></div>
    <div class="foot-addr">
      <svg width="10" height="14" viewBox="0 0 10 14"><path d="M5 0a5 5 0 0 1 5 5c0 4-5 9-5 9S0 9 0 5a5 5 0 0 1 5-5z" fill="#fff"/><circle cx="5" cy="5" r="2" fill="#15164a"/></svg>
      <span>Lorem ipsum dolor sit amet,<br>consectetuer adimpisciged</span>
    </div>
    <div class="foot-contact">
      <div><svg width="12" height="12" viewBox="0 0 12 12"><path d="M2 0l3 0 1 3-2 1c1 2 2 3 4 4l1-2 3 1v3C6 11 1 6 2 0z" fill="#fff"/></svg>123-555-0148</div>
      <div><svg width="12" height="9" viewBox="0 0 12 9"><rect width="12" height="9" fill="#fff"/><path d="M0 0l6 5 6-5" fill="none" stroke="#15164a"/></svg>info@brivanemanagement.com</div>
    </div>
    <div class="subscribe"><div class="field">your e-mail address</div><div class="btn">SUBSCRIBE</div></div>
    <div class="copy">Copyright © 2014 Brivane Management.All Right Reserved</div>
    <div class="social"><span></span><span></span><span></span><span></span></div>
  </footer>

</div>
</body>
</html>
```